Business card design needed

Double sided
Color, unique, elegant

Maybe put this quote somewhere?? But I think it might make it to cluttered?
“The Pilates Method of Body
Conditioning develops the body
uniformly, corrects posture, restores
vitality, invigorates the mind and
elevates the spirit”
- Walter Brennick

Industry/Entity Type

Business

Contact Information for Business Card

Marta Kovalenko
Pilates Instructor & Personal trainer
Mobile: 0498265043
www.qorvith.com.au
email: qorvithwell.motion@mailvex.com

```html
<!DOCTYPE html>
<html lang="en">
<head>
<meta charset="utf-8">
<title>Qorvith – Business Card Set</title>
<link href="https://fonts.googleapis.com/css2?family=Arimo:ital,wght@0,400;1,700&family=Raleway:wght@300&family=Great+Vibes&display=swap" rel="stylesheet">
<style>
  :root{
    --backdrop:#e8e5e0;
    --lime-light:#cadc0c;
    --lime-mid:#b2d01a;
    --lime-deep:#86b52c;
    --stone-light:#b3b1a3;
    --stone-dark:#85847a;
    --stone-shadow:#6a6a61;
    --ink:#3a3a34;
    --ink-soft:#2e2e2a;
    --muted:#8d8c84;
    --rose:#d98ab7;
    --paper:#ffffff;
  }
  *{margin:0;padding:0;box-sizing:border-box}
  html,body{width:1200px;height:1000px;overflow:hidden;background:var(--backdrop)}
  .canvas{position:relative;width:1200px;height:1000px}
  .card{position:absolute;overflow:hidden;box-shadow:0 2px 6px rgba(0,0,0,.18)}
  .card svg{position:absolute;inset:0;display:block}
  .card--portrait{left:96px;top:224px;width:337px;height:551px}
  .card--quote{left:545px;top:138px;width:553px;height:336px}
  .card--contact{left:545px;top:521px;width:553px;height:337px}

  .brand{position:absolute;display:flex;align-items:center;gap:8px;transform:translateX(-50%)}
  .brand__dot{width:10px;height:10px;border-radius:50%;background:var(--paper)}
  .brand__name{font-family:"Raleway",sans-serif;font-weight:300;font-size:22px;letter-spacing:2px;color:var(--paper);text-transform:uppercase}

  .quote{position:absolute;font-family:"Arimo",Arial,sans-serif;font-style:italic;font-weight:700;font-size:11px;line-height:22.5px;color:var(--ink-soft)}
  .signature{position:absolute;font-family:"Great Vibes",cursive;font-size:22px;color:var(--ink-soft)}

  .person{position:absolute;right:50px;top:44px;text-align:right;font-family:"Arimo",Arial,sans-serif}
  .person__name{font-size:26px;line-height:32px;color:var(--ink)}
  .person__surname{color:var(--rose)}
  .person__role{font-size:14px;color:var(--muted);margin-top:2px}
  .contacts{position:absolute;right:57px;top:129px;text-align:right;font-family:"Arimo",Arial,sans-serif;font-size:14px;line-height:27px;color:var(--ink-soft);list-style:none}
  .icon-tab{position:absolute;right:0;top:124px;width:40px;height:84px;border-radius:4px 0 0 4px;background:var(--stone-shadow)}
</style>
</head>
<body>
<main class="canvas">

  <!-- Portrait front -->
  <section class="card card--portrait">
    <svg viewBox="0 0 337 551" width="337" height="551">
      <defs>
        <linearGradient id="limeP" x1="0" y1="0" x2="1" y2="1">
          <stop offset="0" stop-color="var(--lime-light)"/>
          <stop offset=".55" stop-color="var(--lime-mid)"/>
          <stop offset="1" stop-color="var(--lime-deep)"/>
        </linearGradient>
        <linearGradient id="stoneP" x1="1" y1="0" x2="0" y2="1">
          <stop offset="0" stop-color="var(--stone-light)"/>
          <stop offset="1" stop-color="var(--stone-dark)"/>
        </linearGradient>
      </defs>
      <rect width="337" height="551" fill="url(#limeP)"/>
      <path d="M47,551 C32,400 22,250 102,120 C162,40 252,10 337,3 L337,10 C320,120 290,220 200,255 C130,280 70,330 80,420 C85,480 110,530 135,551 Z" fill="var(--stone-shadow)"/>
      <path d="M58,551 C42,400 32,250 110,122 C170,42 260,12 337,5 L337,10 C320,120 290,220 200,255 C130,280 70,330 80,420 C85,480 110,530 135,551 Z" fill="url(#stoneP)"/>
    </svg>
    <div class="brand" style="left:166px;top:158px"><span class="brand__dot"></span><span class="brand__name">Qorvith</span></div>
    <p class="quote" style="left:112px;top:376px">“The Pilates Method of Body<br>Conditioning develops the body<br>uniformly, corrects posture, restores<br>vitality, invigorates the mind and<br>elevates the spirit”</p>
    <p class="signature" style="left:178px;top:492px">Walter Brennick</p>
  </section>

  <!-- Landscape front -->
  <section class="card card--quote">
    <svg viewBox="0 0 553 336" width="553" height="336">
      <defs>
        <linearGradient id="limeL" x1="0" y1="0" x2="1" y2="1">
          <stop offset="0" stop-color="var(--lime-light)"/>
          <stop offset=".6" stop-color="var(--lime-mid)"/>
          <stop offset="1" stop-color="var(--lime-deep)"/>
        </linearGradient>
        <linearGradient id="stoneL" x1="0" y1="0" x2="1" y2="1">
          <stop offset="0" stop-color="var(--stone-dark)"/>
          <stop offset=".5" stop-color="var(--stone-light)"/>
          <stop offset="1" stop-color="var(--stone-dark)"/>
        </linearGradient>
      </defs>
      <rect width="553" height="336" fill="url(#limeL)"/>
      <path d="M0,120 C20,50 70,5 140,0 C230,10 270,120 290,200 C310,260 400,250 553,228 L553,244 C420,288 330,310 250,310 C110,310 20,230 0,182 Z" fill="var(--stone-shadow)"/>
      <path d="M0,110 C20,40 70,5 140,0 C230,10 270,120 290,200 C310,260 400,250 553,228 L553,236 C420,278 330,298 250,298 C110,298 20,220 0,170 Z" fill="url(#stoneL)"/>
    </svg>
    <div class="brand" style="left:160px;top:190px"><span class="brand__dot"></span><span class="brand__name">Qorvith</span></div>
    <p class="quote" style="left:318px;top:68px">“The Pilates Method of Body<br>Conditioning develops the body<br>uniformly, corrects posture, restores<br>vitality, invigorates the mind and<br>elevates the spirit”</p>
    <p class="signature" style="left:388px;top:184px">Walter Brennick</p>
  </section>

  <!-- Landscape back -->
  <section class="card card--contact">
    <svg viewBox="0 0 553 337" width="553" height="337">
      <defs>
        <linearGradient id="limeC" x1="0" y1="0" x2="1" y2="1">
          <stop offset="0" stop-color="var(--lime-light)"/>
          <stop offset=".6" stop-color="var(--lime-mid)"/>
          <stop offset="1" stop-color="var(--lime-deep)"/>
        </linearGradient>
        <linearGradient id="stoneC" x1="0" y1="0" x2="1" y2="1">
          <stop offset="0" stop-color="var(--stone-dark)"/>
          <stop offset=".5" stop-color="var(--stone-light)"/>
          <stop offset="1" stop-color="var(--stone-dark)"/>
        </linearGradient>
      </defs>
      <rect width="553" height="337" fill="url(#limeC)"/>
      <path d="M0,120 C20,50 70,5 140,0 C230,10 270,120 290,200 C310,260 400,250 553,228 L553,244 C420,288 330,310 250,310 C110,310 20,230 0,182 Z" fill="var(--stone-shadow)"/>
      <path d="M0,110 C20,40 70,5 140,0 C230,10 270,120 290,200 C310,260 400,250 553,228 L553,236 C420,278 330,298 250,298 C110,298 20,220 0,170 Z" fill="url(#stoneC)"/>
    </svg>
    <div class="brand" style="left:160px;top:190px"><span class="brand__dot"></span><span class="brand__name">Qorvith</span></div>
    <div class="person">
      <p class="person__name">Marta <span class="person__surname">Kovalenko</span></p>
      <p class="person__role">Pilates Instructor &amp; Personal trainer</p>
    </div>
    <ul class="contacts">
      <li>qorvithwell.motion@mailvex.com</li>
      <li>www.qorvith.com.au</li>
      <li>0498 265 043</li>
    </ul>
    <div class="icon-tab">
      <svg viewBox="0 0 40 84" width="40" height="84" fill="none" stroke="#fff" stroke-width="1.4" stroke-linejoin="round" stroke-linecap="round">
        <rect x="12" y="10" width="16" height="11" rx="1"/>
        <path d="M12,11 L20,17 L28,11"/>
        <circle cx="20" cy="40" r="7.5"/>
        <ellipse cx="20" cy="40" rx="3.2" ry="7.5"/>
        <path d="M12.5,40 H27.5 M14,36 H26 M14,44 H26"/>
        <path d="M15,60 C14,62 15,68 21,73 C24,75 26,75 27,73 L25,70 L22.5,71 C20,69 18.5,67 18,64.5 L19.5,62.5 L17,59.5 Z"/>
      </svg>
    </div>
  </section>

</main>
</body>
</html>
```